WordPress Design for both website and landing page for an expert

I need a clean and stylish design for my new website. I work as an expert (see attached file WHY HOW WHAT), my product is expert opinion (reports) for company evaluations You can use all of the attached pictures colored or black / white. The person is me, you can add other pictures, if you want. The design should be clean and stylish, so you could use white, black, gray, silver and / or one additional color. I have added an idea about my website, see attached file CONCEPT WEBSITE If you have any more information, please do not hesitate to contact us 'Hesitate to ask me ...

```html
<!DOCTYPE html>
<html lang="en">
<head>
<meta charset="utf-8">
<title>Lars Heinemann – About</title>
<link href="https://fonts.googleapis.com/css2?family=Montserrat:wght@200;300;400;600;700&family=Noto+Serif:wght@400&display=swap" rel="stylesheet">
<style>
:root{
  --black:#000000;
  --panel:#1b1b1b;
  --band:#1e1e1e;
  --line:#2c2c2c;
  --white:#ffffff;
  --text:#c9c9c9;
  --muted:#a8a8a8;
  --social:#2e2e2e;
  --photo-a:#7c7a74;
  --photo-b:#d8d4cc;
}
*{margin:0;padding:0;box-sizing:border-box}
html,body{width:1200px;height:2248px;overflow:hidden;background:var(--black)}
body{position:relative;font-family:'Montserrat',sans-serif;color:var(--white)}
.abs{position:absolute}

.brand{left:36px;top:52px;font-weight:600;font-size:20px;letter-spacing:1px;color:var(--white)}
.page-title{left:0;width:1200px;top:58px;text-align:center;font-size:15px;font-weight:600;letter-spacing:2.5px}
.close{left:1119px;top:56px;width:24px;height:24px}

.hero{left:138px;top:197px;width:924px;height:376px;
  background:linear-gradient(90deg,var(--photo-a) 0%,#a7a299 45%,var(--photo-b) 100%)}
.hero-name{left:138px;width:924px;top:325px;text-align:center;font-weight:200;font-size:66px;letter-spacing:9px;color:var(--white)}
.hero-sub{left:138px;width:924px;top:412px;text-align:center;font-weight:400;font-size:25px;color:var(--white)}

.serif{font-family:'Noto Serif',serif;font-size:14.5px;line-height:25.5px;color:var(--text)}
.intro{left:282px;top:638px;width:640px}

.heading{left:0;width:1200px;text-align:center;font-weight:700;font-size:27px;line-height:39px}
.reasons-title{top:766px}

.timeline{left:599px;top:877px;width:2px;height:515px;background:#8a8a8a}
.node{width:68px;height:68px;border-radius:50%;border:1.5px solid #9a9a9a;background:var(--black);display:flex;align-items:center;justify-content:center}
.node--active{background:var(--white);border-color:var(--white)}
.node svg{width:24px;height:24px}
.reason-title{font-weight:700;font-size:16px;letter-spacing:3px}
.reason{width:250px}
.reason--left{text-align:right}

.motives{left:0;top:1462px;width:1200px;height:369px;background:var(--panel)}
.motives-title{top:1523px}
.motive{width:300px}
.motive svg{display:block;width:52px;height:44px;margin-bottom:-4px}
.dot{width:11px;height:11px;border-radius:50%;border:1.5px solid var(--muted)}
.dot--active::after{content:"";position:absolute;left:2.5px;top:2.5px;width:3px;height:3px;border-radius:50%;background:var(--muted)}

.note{left:0;top:1831px;width:1200px;height:68px;background:var(--band);border-top:1px solid var(--line);
  text-align:center;font-size:11.5px;line-height:17px;color:var(--muted);padding-top:17px}
.note b{color:var(--white);font-weight:700}

.cta-title{top:1959px}
.cta-button{left:493px;top:2071px;width:213px;height:39px;border:2px solid var(--white);border-radius:20px;
  text-align:center;line-height:35px;font-weight:700;font-size:12px;letter-spacing:1px}

.footer{left:0;top:2180px;width:1200px;height:68px;background:var(--panel)}
.copyright{left:136px;top:2206px;font-size:12.5px;letter-spacing:1px;color:var(--muted)}
.social{width:42px;height:42px;border-radius:50%;background:var(--social);top:2193px}
</style>
</head>
<body>

<header>
  <div class="abs brand">Heinemann</div>
  <div class="abs page-title">ABOUT</div>
  <svg class="abs close" viewBox="0 0 24 24" aria-label="Close"><path d="M2 2L22 22M22 2L2 22" stroke="#fff" stroke-width="2.2"/></svg>
</header>

<section>
  <div class="abs hero" role="img" aria-label="Portrait of the expert in a dark suit in a bright modern hallway"></div>
  <div class="abs hero-name">LARS HEINEMANN</div>
  <div class="abs hero-sub">Expert for company valuations</div>
</section>

<p class="abs serif intro">Sed ut perspiciatis unde omnis iste natus&nbsp; voluptatem accusantium doloremque laudan-<br>tium, totam rem aperiam, eaque ipsa quae inventore veritatis et quasi architecto<br>beatae vitae dicta sunt explicabo.</p>

<section class="reasons">
  <h2 class="abs heading reasons-title">3 reasons, Why you should<br>work with me.</h2>
  <div class="abs timeline"></div>

  <div class="abs node" style="left:566px;top:920px">
    <svg viewBox="0 0 24 24" fill="none" stroke="#fff" stroke-width="1.5"><rect x="3" y="4" width="18" height="17"/><path d="M3 9H21M8 2V6M16 2V6"/><path d="M7 13h2M11 13h2M15 13h2M7 17h2M11 17h2M15 17h2"/></svg>
  </div>
  <div class="abs reason" style="left:669px;top:920px">
    <div class="reason-title">FAST PROCESS</div>
    <p class="serif">You will receive your report promptly (within a maximum of 21 days after receipt of all required documents)</p>
  </div>

  <div class="abs node node--active" style="left:566px;top:1074px">
    <svg viewBox="0 0 24 24" fill="none" stroke="#000" stroke-width="1.5"><circle cx="12" cy="9" r="6"/><path d="M8 14L6 21L9 19.5L10.5 22L12 16M16 14L18 21L15 19.5L13.5 22L12 16"/></svg>
  </div>
  <div class="abs reason reason--left" style="left:277px;top:1074px">
    <div class="reason-title">CERTIFIED</div>
    <p class="serif">You receive a qualified and reliable report from a certified expert (highest acceptance by all parties)</p>
  </div>

  <div class="abs node" style="left:566px;top:1228px">
    <svg viewBox="0 0 24 24" fill="none" stroke="#fff" stroke-width="1.5"><rect x="3" y="10" width="4" height="11"/><path d="M7 11L11 3C13 3 14 4.5 13.5 6.5L13 9H19C20.5 9 21.3 10.3 21 11.5L19.5 19C19.2 20.2 18.3 21 17 21H7"/></svg>
  </div>
  <div class="abs reason" style="left:669px;top:1228px">
    <div class="reason-title">UNDERSTANDABLE</div>
    <p class="serif">Your report will be logical and comprehensible for you and will not contain any "technical Chinese"</p>
  </div>
</section>

<section class="abs motives"></section>
<h2 class="abs heading motives-title">What are the buying motives<br>of the customers?</h2>
<div class="abs motive" style="left:282px;top:1623px">
  <svg viewBox="0 0 52 44" fill="none" stroke="#000" stroke-width="3"><circle cx="24" cy="22" r="20"/><path d="M13 21L22 30L48 4"/></svg>
  <p class="serif">You want to transfer your business<br>to your heirs and need a valuation for<br>the tax office?</p>
</div>
<div class="abs motive" style="left:634px;top:1623px">
  <svg viewBox="0 0 52 44" fill="none" stroke="#000" stroke-width="3"><circle cx="24" cy="22" r="20"/><path d="M13 21L22 30L48 4"/></svg>
  <p class="serif">You have to pay someone in the<br>context of a separation / divorce and<br>need a tax base?</p>
</div>
<div class="abs dot dot--active" style="left:584px;top:1775px"></div>
<div class="abs dot" style="left:605px;top:1775px"></div>

<div class="abs note"><b>Note:</b> The cost of a report are always disproportionately cheaper than the cost of legal disputes.<br>And that detached from the psychological burden of such an argument ...</div>

<section>
  <h2 class="abs heading cta-title">You need an opinion to determine<br>the value of your company</h2>
  <div class="abs cta-button">CONTACT NOW!</div>
</section>

<footer class="abs footer"></footer>
<div class="abs copyright">Copyright © 2018 Lars Heinemann. All Rights Reserved</div>
<div class="abs social" style="left:916px" aria-label="Social link"></div>
<div class="abs social" style="left:969px" aria-label="Social link"></div>
<div class="abs social" style="left:1020px" aria-label="Social link"></div>

</body>
</html>
```